Business card design for holistic health care clinic

We need a double-sided business card design for our holistic health care clinic that integrates our logo design and also its color scheme. My business is called Valmira. It is an integrative medicine clinic. You have already done the logo for me. Please ensure an elegant and upscale design that is not cluttered, but still has all the necessary information (please see below for details).

Target Market(s)

Wellness, fitness, rehabilitation for educated, well-traveled open-minded clients who are focused on natural, organic, balanced and preventive healthcare and lifestyle.

Industry/Entity Type

Medical

Contact Information for Business Card

Modern, clean.

Number of Pages Required

1 page

Font styles to use
Serif
Sans Serif

Colors

Designer to choose colors to be used in the design.

Requirements
Must have
• Logo on one side, all other information on the other side.
• Other information should include:
• Tobias Wrenfeld - DOE, CPT, LMT
• 4100 East Marrow Drive
• Austin, TX 78119
• 512 555 0148
• 818 555 0192
• info@ValmiraHealth.example
• t.wrenfeld@ValmiraHealth.example
Nice to have
• Darker background on front - but not totally black - shaded/dark gray.

```html
<!DOCTYPE html>
<html lang="en">
<head>
<meta charset="utf-8">
<title>Valmira – Business Card</title>
<link rel="stylesheet" href="https://fonts.googleapis.com/css2?family=Source+Sans+3:wght@400;600;700&display=swap">
<style>
  :root {
    --page-bg: #e9e7e4;
    --card-dark: #0e0f11;
    --card-mid: #2a2c30;
    --brand-blue: #2f86cc;
    --brand-blue-deep: #16558f;
    --text-light: #d9dadc;
    --text-soft: #a9acb1;
  }
  * { box-sizing: border-box; margin: 0; padding: 0; }
  html, body {
    width: 1200px; height: 969px; overflow: hidden;
    background: var(--page-bg);
    font-family: "Source Sans 3", Arial, sans-serif;
  }
  .canvas {
    width: 1200px; height: 969px;
    display: flex; align-items: center; justify-content: center;
  }
  .card {
    position: relative;
    width: 1040px; height: 592px;
    background: linear-gradient(120deg, var(--card-mid) 0%, #1a1b1e 45%, var(--card-dark) 80%);
    border-radius: 4px;
    box-shadow: 0 18px 40px rgba(0,0,0,.25);
    overflow: hidden;
  }
  .brand-decoration {
    position: absolute; top: 0; right: 0;
    width: 592px; height: 100%;
    background:
      radial-gradient(ellipse 60% 45% at 62% 28%, rgba(47,134,204,.85) 0%, rgba(22,85,143,.55) 50%, rgba(14,15,17,0) 100%),
      radial-gradient(ellipse 22% 55% at 92% 65%, rgba(47,134,204,.7) 0%, rgba(22,85,143,.35) 60%, rgba(14,15,17,0) 100%);
  }
  .brand {
    position: absolute; left: 44px; top: 92px;
  }
  .brand-name {
    font-weight: 700; font-size: 84px; letter-spacing: 2px;
    color: var(--brand-blue); line-height: 1;
    text-transform: uppercase;
  }
  .brand-tagline {
    margin-top: 8px;
    font-weight: 600; font-size: 23px; letter-spacing: .6px;
    color: var(--brand-blue);
  }
  .person-name {
    position: absolute; left: 44px; top: 282px;
    font-weight: 700; font-size: 29px; letter-spacing: .5px;
    color: var(--brand-blue); text-transform: uppercase; white-space: nowrap;
  }
  .person-creds { font-size: 17px; font-weight: 600; margin-left: 2px; }
  .address {
    position: absolute; left: 44px; top: 338px;
    font-style: normal; color: var(--text-light);
    font-size: 25px; line-height: 35px;
  }
  .contact-list {
    position: absolute; left: 44px; top: 422px;
    list-style: none; color: var(--text-light);
  }
  .contact-list li {
    display: flex; align-items: center; gap: 14px;
    font-size: 25px; line-height: 33px; white-space: nowrap;
  }
  .contact-list .email, .contact-list .web { color: var(--text-soft); }
  .contact-icon { width: 20px; height: 20px; fill: var(--brand-blue); flex: none; }
</style>
</head>
<body>
<main class="canvas">
  <section class="card">
    <div class="brand-decoration" role="img" aria-label="Large blue winged brand emblem decoration"></div>

    <header class="brand">
      <div class="brand-name">Valmira</div>
      <div class="brand-tagline">Integrative Holistic Medicine</div>
    </header>

    <div class="person-name">Tobias Wrenfeld <span class="person-creds">- DOE, CPT, LMT</span></div>

    <address class="address">
      4100 East Marrow Drive<br>
      Austin, TX 78119
    </address>

    <ul class="contact-list">
      <li>
        <svg class="contact-icon" viewBox="0 0 20 20" aria-hidden="true"><path d="M3 6c0-2 2-3 7-3s7 1 7 3v2h-4V6.5H7V8H3z M5 9h10l2 8H3z"/></svg>
        512 555 0148
      </li>
      <li>
        <svg class="contact-icon" viewBox="0 0 20 20" aria-hidden="true"><path d="M6 1h8a1.5 1.5 0 0 1 1.5 1.5v15A1.5 1.5 0 0 1 14 19H6a1.5 1.5 0 0 1-1.5-1.5v-15A1.5 1.5 0 0 1 6 1zm0.5 2.5v12h7v-12z"/></svg>
        818 555 0192
      </li>
      <li class="email">
        <svg class="contact-icon" viewBox="0 0 20 20" aria-hidden="true"><path d="M2 5h16v10H2z"/><path d="M2 5l8 6l8-6" stroke="#121315" stroke-width="1.4" fill="none"/></svg>
        t.wrenfeld@ValmiraHealth.example
      </li>
      <li class="web">
        <svg class="contact-icon" viewBox="0 0 20 20" aria-hidden="true"><circle cx="10" cy="10" r="8"/><path d="M2 10h16M10 2c3 3 3 13 0 16M10 2c-3 3-3 13 0 16" stroke="#121315" stroke-width="1.2" fill="none"/></svg>
        www.ValmiraHealth.example
      </li>
    </ul>
  </section>
</main>
</body>
</html>
```